Business Cards for IT Consulting Company (Managed Service Provider)

I am looking to have some business cards printed and would like some designs. We are an IT Consulting company based in Vancouver BC. I would like a nice clean and modern look to the cards. I have uploaded all the versions of my logo so parts can be used as needed. Here is a snippit from our website homepage:

Quillbrook Networks Ltd. is an IT Solutions Partner located in Vancouver BC, Canada. We offer IT solutions and support to customers in the greater Vancouver Area. With expertise in Microsoft platforms, as well as Linux and Mac OSX and over 12 years experience in the IT industry, Quillbrook Networks is dedicated to offering our clients top quality service and products. We take pride in the solutions we offer our customers. The greatest compliment a client can give us is to recommend our services.

Quillbrook Networks Ltd. offers a wide range of IT services from onsite service to remote support and managed service solutions. This allows clients to choose the support path that best suits their company’s needs. Supporting many different sized companies from small to enterprise level over the past 12 years Quillbrook Networks has the experience and expertise needed to ensure things run smoothly. Allowing our clients to focus on doing business.

Revolutionizing the way IT services are delivered.

Quillbrook Networks is dedicated to providing our clients with IT solutions that work and grow with them for years to come. This philosophy helps save money in the long run instead of replacing equipment constantly. Far too often IT solutions are not well thought out and while possibly solving the problem at hand, require replacement due to growth or quality within a very short time frame. Quillbrook Networks takes pride in providing solutions that will last and be able to accommodate growth without the need for replacement.

Industry/Entity Type

Information Technology

Contact Information for Business Card

Quillbrook Networks Ltd.
(Employee Name)
Eml: (Employees Email Address)
Web: quillbrook.me
Ph: 604-555-0148

Font styles to use
Serif
Sans Serif

Requirements
Must have
• The Company logo and company colors.
Nice to have
• - Our tag line: "Revolutionizing IT Services" or "Revolutionizing the way IT services are delivered."
• - Also I really like the idea of nature and technology together blending which is sort of where my logo came from so integrating that somehow onto the business cards would be great.

```html
<!DOCTYPE html>
<html lang="en">
<head>
<meta charset="utf-8">
<title>Quillbrook Networks Ltd. — Business Cards</title>
<link href="https://fonts.googleapis.com/css2?family=Montserrat:wght@400;500;600;700&display=swap" rel="stylesheet">
<style>
  :root {
    --ink: #000000;
    --paper: #ffffff;
    --brand-blue: #1fa3e6;
    --band-text: #1a1a1a;
    --backdrop: #3a3a3a;
  }
  * { margin: 0; padding: 0; box-sizing: border-box; }
  html, body { width: 1200px; height: 900px; overflow: hidden; }
  body {
    background: var(--backdrop);
    font-family: "Montserrat", Arial, sans-serif;
    position: relative;
  }
  .card {
    position: absolute;
    width: 560px;
    height: 320px;
    background: var(--ink);
    color: var(--paper);
    overflow: hidden;
  }
  /* Back side */
  .card--back { left: 80px; top: 90px; }
  .back-brand {
    position: absolute;
    top: 100px; left: 0; right: 0;
    display: flex; align-items: center; justify-content: center; gap: 14px;
    font-size: 28px; font-weight: 600; color: var(--paper);
  }
  .brand-square { width: 22px; height: 22px; background: var(--brand-blue); }
  .back-rule {
    position: absolute; top: 254px; height: 1px; background: var(--paper);
  }
  .back-rule--left { left: 0; width: 190px; }
  .back-rule--right { right: 0; width: 190px; }
  .back-url {
    position: absolute; top: 245px; left: 0; right: 0;
    text-align: center; font-size: 13px; font-weight: 600; letter-spacing: 1.5px;
  }
  .back-url .accent { color: var(--brand-blue); }

  /* Front side */
  .card--front { left: 560px; top: 490px; }
  .front-brand {
    position: absolute; top: 40px; left: 36px;
    display: flex; align-items: center; gap: 12px;
    font-size: 24px; font-weight: 600; color: var(--brand-blue);
  }
  .tagline-band {
    position: absolute; top: 126px; left: 0;
    width: 410px; height: 46px;
    background: var(--paper);
    clip-path: polygon(0 0, 100% 0, 94% 100%, 0 100%);
    display: flex; align-items: center; padding-left: 36px;
    font-size: 17px; font-weight: 500; color: var(--band-text); letter-spacing: 0.5px;
  }
  .person { position: absolute; top: 194px; left: 36px; }
  .person-name {
    font-size: 18px; font-weight: 700; color: var(--brand-blue); letter-spacing: 1.5px;
  }
  .person-title {
    font-size: 11px; font-weight: 600; letter-spacing: 1px; margin-top: 2px;
  }
  .contacts { list-style: none; margin-top: 8px; }
  .contacts li {
    display: flex; align-items: center; gap: 9px;
    font-size: 12.5px; font-weight: 500; letter-spacing: 0.5px; line-height: 20px;
  }
  .contact-icon { width: 11px; height: 11px; flex: none; }
</style>
</head>
<body>
  <section class="card card--back" aria-label="Business card back">
    <div class="back-brand"><span class="brand-square"></span>Quillbrook Networks Ltd.</div>
    <span class="back-rule back-rule--left"></span>
    <span class="back-rule back-rule--right"></span>
    <p class="back-url">www.<span class="accent">quillbrook</span>.me</p>
  </section>

  <section class="card card--front" aria-label="Business card front">
    <div class="front-brand"><span class="brand-square"></span>Quillbrook Networks Ltd.</div>
    <div class="tagline-band">Revolutionizing IT Services</div>
    <div class="person">
      <p class="person-name">MAREN OKAFOR</p>
      <p class="person-title">DIRECTOR</p>
      <ul class="contacts">
        <li>
          <svg class="contact-icon" viewBox="0 0 24 24" aria-hidden="true"><path fill="#1fa3e6" d="M6.6 10.8a15.1 15.1 0 0 0 6.6 6.6l2.2-2.2a1 1 0 0 1 1-.25 11.4 11.4 0 0 0 3.6.57 1 1 0 0 1 1 1V20a1 1 0 0 1-1 1A17 17 0 0 1 3 4a1 1 0 0 1 1-1h3.5a1 1 0 0 1 1 1c0 1.25.2 2.45.57 3.57a1 1 0 0 1-.25 1z"/></svg>
          604-555-0148
        </li>
        <li>
          <svg class="contact-icon" viewBox="0 0 24 24" aria-hidden="true"><rect x="2" y="5" width="20" height="14" fill="none" stroke="#1fa3e6" stroke-width="2"/><path d="M2 5l10 8 10-8" fill="none" stroke="#1fa3e6" stroke-width="2"/></svg>
          info@marenokafor.com
        </li>
        <li>
          <svg class="contact-icon" viewBox="0 0 24 24" aria-hidden="true"><circle cx="12" cy="12" r="10" fill="none" stroke="#1fa3e6" stroke-width="2"/><path d="M2 12h20M12 2c3 3 3 17 0 20M12 2c-3 3-3 17 0 20" fill="none" stroke="#1fa3e6" stroke-width="2"/></svg>
          www.quillbrook.me
        </li>
      </ul>
    </div>
  </section>
</body>
</html>
```